Etiketten für Olivenöl-Intensivcreme
Zielgruppe
Wir produzieren Bio-Food, u.a. Wein und Olivenöl. Jetzt soll eine Olivenöl-Intensivcreme im Bereich Kosmetik auf dem Markt platziert werden. Unsere Zielgruppe hat ein sehr breites Altersspektrum (jung bis alt), ist naturverbunden, tierlieb, gebildet, kritisch-reflektierend, weiß gute Qualität zu schätzen, ist überwiegend weiblich. Die Olivenöl-Intensivcreme hat eine sehr breite Verwendung und soll sich als 'Allzweckwaffe' in jedem Haushalt etablieren (Babyhaut-Pflege, Lippenpflege, Ganzkörperpflege, Hand-Schutzcreme etc.).
Aufgabenstellung
Die Creme soll heißen: Velamira (es könnte z.B. der Buchstabe 'O' durch eine Olive ersetzt werden). Es gibt zwei Etikette (Deckeloberseite der Metalldose und auf dem Boden). Der Durchmesser der Etikette ist jeweils 5,5 cm. Die Deckelunterseite gilt reinen Pflichtangaben. Im Dateidownloadbereich sind die Textvorgaben für die Etikette. MUT zur Farbe! Wir sind NICHT brav und angepasst! Orange kann Akzente setzen bzw. für Aufmerksamkeit im Regal sorgen.

```html
<!DOCTYPE html>
<html lang="de">
<head>
<meta charset="utf-8">
<title>Velamira – Etiketten</title>
<link rel="stylesheet" href="https://fonts.googleapis.com/css2?family=Josefin+Sans:wght@300;400&family=Great+Vibes&display=swap">
<style>
  :root {
    --gold: #b08a1a;
    --label: #ffffff;
    --stage: #d9d9d9;
    --art: #e3d3a5;
  }
  * { box-sizing: border-box; margin: 0; padding: 0; }
  html, body { width: 1200px; height: 1200px; overflow: hidden; }
  body {
    background: var(--stage);
    font-family: "Josefin Sans", sans-serif;
    color: var(--gold);
    position: relative;
  }
  .label {
    position: absolute;
    top: 320px;
    width: 560px;
    height: 560px;
    border-radius: 50%;
    background: var(--label);
    font-variant: small-caps;
    text-align: center;
  }
  .label--lid { left: 25px; }
  .label--base { left: 615px; }
  .abs { position: absolute; left: 0; right: 0; }

  .mascot {
    position: absolute;
    left: 50%;
    transform: translateX(-50%);
    width: 54px;
    height: 66px;
    border-radius: 10px;
    background: linear-gradient(160deg, var(--art), #f3ead2);
  }
  .brand { font-size: 27px; letter-spacing: 0.5px; font-variant: normal; }
  .wordmark {
    font-family: "Great Vibes", cursive;
    font-variant: normal;
    font-size: 138px;
    line-height: 1;
  }
  .band {
    position: absolute;
    left: 50%;
    transform: translateX(-50%);
    background: var(--gold);
    color: var(--label);
    border-radius: 22px;
    white-space: nowrap;
  }
  .band--lid { width: 470px; height: 44px; font-size: 29px; line-height: 50px; letter-spacing: 1.5px; }
  .band--base { width: 408px; height: 23px; font-size: 19px; line-height: 26px; border-radius: 12px; }
  .claim { font-size: 28px; letter-spacing: 1px; }
  .badges {
    position: absolute;
    top: 415px;
    left: 170px;
    font-size: 22px;
    line-height: 24px;
    text-align: center;
    width: 110px;
  }
  .olive-art {
    position: absolute;
    top: 402px;
    left: 290px;
    width: 100px;
    height: 64px;
    border-radius: 32px;
    background: linear-gradient(135deg, var(--art), #f1e6c7);
  }
  .arc { position: absolute; inset: 0; }
  .arc text { font-family: "Josefin Sans", sans-serif; font-variant: small-caps; font-size: 27px; fill: var(--gold); letter-spacing: 1.5px; }

  .copy { font-size: 21px; line-height: 26px; }
  .copy u { text-underline-offset: 3px; text-decoration-thickness: 1px; }
  .recycle {
    position: absolute;
    top: 408px;
    left: 80px;
    width: 44px;
    height: 44px;
    border-radius: 50%;
    background: var(--gold);
  }
  .imprint { font-size: 18px; line-height: 22px; }
  .volume { position: absolute; top: 418px; left: 425px; font-size: 28px; line-height: 24px; }
  .volume small { display: block; font-size: 20px; }
  .small { font-size: 17px; line-height: 21px; }
</style>
</head>
<body>

<section class="label label--lid" aria-label="Deckeletikett">
  <div class="mascot" style="top:28px" role="img" aria-label="Markenzeichen-Illustration"></div>
  <div class="abs brand" style="top:110px">MIRETO.LAND</div>
  <div class="abs wordmark" style="top:142px">Velamira</div>
  <div class="band band--lid" style="top:293px">Olivenöl-Intensivcreme</div>
  <div class="abs claim" style="top:358px">Naturkosmetik</div>
  <div class="badges">Bio-Olive<br>Vegan</div>
  <div class="olive-art" role="img" aria-label="Illustration Olivenzweig"></div>
  <svg class="arc" viewBox="0 0 560 560" aria-hidden="false">
    <defs>
      <path id="lid-arc" d="M 60 330 A 225 225 0 0 0 500 330"/>
    </defs>
    <text><textPath href="#lid-arc" startOffset="50%" text-anchor="middle">Pflege- und Schutzcreme</textPath></text>
  </svg>
</section>

<section class="label label--base" aria-label="Bodenetikett">
  <div class="mascot" style="top:22px;width:44px;height:56px" role="img" aria-label="Markenzeichen-Illustration"></div>
  <div class="abs brand" style="top:90px;font-size:24px">MIRETO.LAND</div>
  <div class="band band--base" style="top:127px">wasserfreie Creme, unparfümiert</div>
  <div class="abs copy" style="top:162px"><u>Ingredients:</u> Olea Europaea Fruit Oil,<br>Hydrogenated Rapeseed Oil, Tocopherol</div>
  <div class="abs copy" style="top:220px"><u>Anwendung:</u> sparsam auf die trockene<br>Haut auftragen (ergiebig!). Die Einwirkzeit<br>kann einige Minuten dauern, vorher kann es<br>beim Berühren von Gegenständen mit den<br>gecremten Körperpartien<br>zur Fettübertragung kommen.</div>
  <div class="recycle" role="img" aria-label="Recyclingzeichen"></div>
  <div class="abs imprint" style="top:386px">MIRETO.LAND<br>Dr. med. Lena Holmer<br>Lindenweg 27 · D-24100 Nordstadt<br>www.mireto.land</div>
  <div class="volume">150<small>ml</small></div>
  <div class="abs small" style="top:484px">Mind. haltbar: Januar 2021<br>Made in Germany</div>
</section>

</body>
</html>
```